Harbourline Electrical Solutions

On one side. LOGO (underneath:) Commercial Industrial Residential

- NAME & CONTACT DETAILS

Marcus T. Hollings
Project Manager

(Cell icon) (441) 555-0187
(Email icon) hlelectricalsolutions@mailvento.com
(Facebook & Instagram icons )@hlelectricalsolutions

Other side: LOGO - underneath ELECTRICAL CONSTRUCTION & MAINTENANCE . LED LIGHTING & AUTOMATION . LIFE SAFETY SYSTEMS (FIRE ALARM / SECURITY) . DATA & COMMUNICATION

```html
<!DOCTYPE html>
<html lang="en">
<head>
<meta charset="utf-8">
<title>Harbourline Electrical Solutions – Business Card</title>
<link rel="stylesheet" href="https://fonts.googleapis.com/css2?family=Montserrat:wght@500;600;700&family=Roboto:wght@400&family=Exo+2:ital,wght@1,700&display=swap">
<style>
  :root {
    --ink-blue: #0b5577;
    --band-grey: #3f4547;
    --page: #2e2f31;
    --paper: #ffffff;
    --text-dark: #2b2b2b;
    --rule-white: #ffffff;
  }
  * { box-sizing: border-box; margin: 0; padding: 0; }
  html, body {
    width: 799px; height: 1200px; overflow: hidden;
    background: var(--page);
  }
  .sheet {
    position: relative; width: 799px; height: 1200px;
  }
  .card {
    position: absolute; left: 50px; width: 700px; height: 400px;
    overflow: hidden;
    box-shadow: 0 10px 24px rgba(0,0,0,.45);
  }

  /* ---------- Front ---------- */
  .card--front { top: 120px; background: var(--ink-blue); color: var(--rule-white); }
  .front__brand {
    position: absolute; left: 0; right: 0; top: 58px;
    text-align: center;
    font-family: "Montserrat", sans-serif; font-weight: 600;
    font-size: 30px; letter-spacing: 5px; line-height: 1.25;
    text-transform: uppercase;
  }
  .front__band {
    position: absolute; left: 0; right: 0; top: 205px; height: 95px;
    background: var(--band-grey);
    display: flex; flex-direction: column; justify-content: center; align-items: center;
    font-family: "Roboto", sans-serif; font-size: 17px; line-height: 1.6;
  }
  .front__band .sep { margin: 0 8px; }
  .front__social {
    position: absolute; left: 0; right: 0; top: 322px;
    text-align: center;
    font-family: "Roboto", sans-serif; font-size: 17px;
  }

  /* ---------- Back ---------- */
  .card--back { top: 680px; background: var(--paper); }
  .back__wave { position: absolute; inset: 0; width: 700px; height: 400px; }
  .back__brand {
    position: absolute; left: 150px; top: 34px;
    font-family: "Montserrat", sans-serif; font-weight: 600;
    font-size: 24px; letter-spacing: 4px; line-height: 1.25;
    text-transform: uppercase; color: var(--ink-blue);
  }
  .back__sectors {
    position: absolute; left: 90px; top: 128px;
    font-family: "Montserrat", sans-serif; font-weight: 700;
    font-size: 13px; letter-spacing: 2.5px; color: var(--ink-blue);
  }
  .back__sectors .sep { margin: 0 14px; color: var(--text-dark); font-weight: 500; }
  .contact {
    position: absolute; left: 70px; top: 168px;
    list-style: none;
    font-family: "Roboto", sans-serif; font-size: 16px; color: var(--text-dark);
  }
  .contact li { display: flex; align-items: center; gap: 10px; height: 27px; }
  .contact svg { width: 15px; height: 15px; fill: var(--text-dark); }
  .contact .no-icon { padding-left: 25px; }
  .person {
    position: absolute; right: 48px; top: 300px;
    text-align: right; color: var(--rule-white);
  }
  .person__name {
    font-family: "Exo 2", sans-serif; font-style: italic; font-weight: 700; font-size: 27px;
  }
  .person__role {
    font-family: "Roboto", sans-serif; font-size: 17px; margin-top: 2px;
  }
</style>
</head>
<body>
<main class="sheet">

  <section class="card card--front">
    <div class="front__brand">Harbourline<br>Electrical Solutions</div>
    <div class="front__band">
      <p>Electrical Construction &amp; Maintenance<span class="sep">|</span>Led Lighting &amp; Automation</p>
      <p>Life Safety Systems (Fire Alarm/Security)<span class="sep">|</span>Data &amp; Communication</p>
    </div>
    <p class="front__social">@hlelectricalsolutions</p>
  </section>

  <section class="card card--back">
    <svg class="back__wave" viewBox="0 0 700 400" aria-hidden="true">
      <path d="M0 250 C90 305 200 335 340 322 C480 310 570 262 700 252 L700 400 L0 400 Z" fill="var(--ink-blue)"/>
      <path d="M0 222 C95 300 235 312 380 296 C520 280 600 238 700 226" fill="none" stroke="var(--band-grey)" stroke-width="12"/>
      <path d="M0 232 C95 310 235 322 380 306 C520 290 600 248 700 236" fill="none" stroke="var(--paper)" stroke-width="7"/>
    </svg>

    <div class="back__brand">Harbourline<br>Electrical Solutions</div>
    <p class="back__sectors">COMMERCIAL<span class="sep">|</span>INDUSTRIAL<span class="sep">|</span>RESIDENTIAL</p>

    <ul class="contact">
      <li>
        <svg viewBox="0 0 24 24" aria-hidden="true"><path d="M6.6 10.8a15.1 15.1 0 0 0 6.6 6.6l2.2-2.2a1 1 0 0 1 1-.25 11.4 11.4 0 0 0 3.6.57 1 1 0 0 1 1 1V20a1 1 0 0 1-1 1A17 17 0 0 1 3 4a1 1 0 0 1 1-1h3.5a1 1 0 0 1 1 1c0 1.25.2 2.45.57 3.57a1 1 0 0 1-.25 1z"/></svg>
        (441) 555-0187
      </li>
      <li>
        <svg viewBox="0 0 24 24" aria-hidden="true"><path d="M2 5h20v14H2z M3.5 6.5 12 13l8.5-6.5" fill="none" stroke="#2b2b2b" stroke-width="2"/></svg>
        hlelectricalsolutions@mailvento.com
      </li>
      <li class="no-icon">@hlelectricalsolutions</li>
    </ul>

    <div class="person">
      <p class="person__name">Marcus T. Hollings</p>
      <p class="person__role">Project Manager</p>
    </div>
  </section>

</main>
</body>
</html>
```